Indy Film Production Company/Studio

We need a business card designed from an existing logo. We are a digital studio/production company that caters to creating genre entertainment, like Action, Horror, and martial arts. The card along with the logo will be used to Brand the company from letter heads to banners. The design will also be used for postcards and Brochures. It should be professional and masculine.
Updates

Thank you to all the designers who have participated. I'm narrowing down who it will be. Thank you again.

Target Market(s)

Investors, Networks, Producers, and actors

Industry/Entity Type

Film Production

Contact Information for Business Card

Teodoro Valbuena
Producer/Writer/Director
www.kestrelpicturehouse.example

Requirements
Must have
• Website address, Facebook icon and Twitter icon possibly in the back of the card.
Nice to have
• Logline of Company: Follow The Action.

```html
<!DOCTYPE html>
<html lang="en">
<head>
<meta charset="utf-8">
<title>Kestrel Picture House – Business Card</title>
<link rel="stylesheet" href="https://fonts.googleapis.com/css2?family=Oswald:wght@700&family=Roboto:wght@400;500&display=swap">
<style>
  :root {
    --brand-red: #e31b23;
    --brand-red-dark: #a8141a;
    --card-white: #ffffff;
    --ink: #3a3a3a;
    --ink-soft: #555555;
    --backdrop: #d9d9d9;
  }
  * { box-sizing: border-box; margin: 0; padding: 0; }
  html, body {
    width: 1200px; height: 950px; overflow: hidden;
    background: var(--backdrop);
    font-family: "Roboto", Arial, sans-serif;
  }
  .sheet {
    position: relative; width: 1200px; height: 950px;
  }
  .card {
    position: absolute; left: 250px; width: 700px; height: 400px;
    box-shadow: 0 6px 18px rgba(0,0,0,0.25);
    overflow: hidden;
  }
  /* Back side */
  .card--back {
    top: 50px;
    background: linear-gradient(135deg, var(--brand-red) 0%, #d0161d 55%, var(--brand-red-dark) 100%);
    color: var(--card-white);
  }
  .card--back .wordmark {
    position: absolute; left: 0; right: 0; top: 150px;
    text-align: center;
    font-family: "Oswald", Impact, sans-serif; font-weight: 700;
    font-size: 46px; letter-spacing: 3px; text-transform: uppercase;
    color: var(--card-white);
  }
  .card--back .web {
    position: absolute; left: 0; right: 0; top: 232px;
    text-align: center; font-size: 18px; letter-spacing: 1.5px;
    color: rgba(255,255,255,0.92);
  }
  .social {
    position: absolute; top: 26px; right: 28px; display: flex; gap: 6px;
  }
  .social__tile {
    width: 24px; height: 24px; background: rgba(255,255,255,0.9);
  }
  /* Front side */
  .card--front {
    top: 500px; background: var(--card-white);
  }
  .card--front .wordmark {
    position: absolute; left: 44px; top: 40px;
    font-family: "Oswald", Impact, sans-serif; font-weight: 700;
    font-size: 40px; letter-spacing: 2px; text-transform: uppercase;
    color: var(--brand-red); line-height: 1.1;
  }
  .contacts {
    position: absolute; left: 44px; top: 200px; list-style: none;
    font-size: 17px; color: var(--ink-soft);
  }
  .contacts li { display: flex; align-items: center; gap: 10px; margin-bottom: 9px; }
  .contacts svg { width: 16px; height: 16px; fill: var(--brand-red); flex: none; }
  .person {
    position: absolute; right: 76px; bottom: 52px; text-align: right;
  }
  .person__name {
    font-size: 24px; font-weight: 500; color: var(--brand-red); letter-spacing: 0.5px;
  }
  .person__role {
    font-size: 18px; color: var(--ink); margin-top: 4px; letter-spacing: 0.5px;
  }
  .edge-tab {
    position: absolute; right: 0; bottom: 34px; width: 18px; height: 48px;
    background: var(--brand-red);
  }
</style>
</head>
<body>
<main class="sheet">
  <section class="card card--back" aria-label="Card back">
    <div class="social" aria-label="Social media">
      <span class="social__tile"></span>
      <span class="social__tile"></span>
    </div>
    <h2 class="wordmark">Kestrel Picture House</h2>
    <p class="web">www.kestrelpicturehouse.example</p>
  </section>

  <section class="card card--front" aria-label="Card front">
    <h1 class="wordmark">Kestrel<br>Picture House</h1>
    <ul class="contacts">
      <li>
        <svg viewBox="0 0 16 16"><path d="M3 2h3l1 3-2 1.5a9 9 0 0 0 4.5 4.5L11 9l3 1v3a1 1 0 0 1-1 1A12 12 0 0 1 2 3a1 1 0 0 1 1-1z"/></svg>
        <span>555 0142 7788</span>
      </li>
      <li>
        <svg viewBox="0 0 16 16"><path d="M1 3h14v10H1z M1 3l7 6 7-6" fill="none" stroke="#e31b23" stroke-width="1.6"/><rect x="1" y="3" width="14" height="10" fill="#e31b23"/><path d="M1.5 3.5l6.5 5.5 6.5-5.5" fill="none" stroke="#fff" stroke-width="1.4"/></svg>
        <span>teo@kestrel.example</span>
      </li>
      <li>
        <svg viewBox="0 0 16 16"><circle cx="8" cy="8" r="7"/><path d="M1 8h14M8 1c3 3 3 11 0 14M8 1c-3 3-3 11 0 14" fill="none" stroke="#fff" stroke-width="1.1"/></svg>
        <span>www.kestrelpicturehouse.example</span>
      </li>
    </ul>
    <div class="person">
      <p class="person__name">Teodoro Valbuena</p>
      <p class="person__role">Producer/Writer/Director</p>
    </div>
    <span class="edge-tab"></span>
  </section>
</main>
</body>
</html>
```